Restaurant Menu New Design

Hello Designers,

Blue Fern is a casual family oriented dine-in restaurant, we serve American Italian dishes like Pizza, Pasta, and Sandwiches.

We are excited about adding some new delicious dishes and recipes to our menu. And we are looking for a talented and creative designer to design it.

The menu is a 12 page black leather book, page size is:
6.5" X 11.69" (16.51 cm X 29.69 cm)

Below is the scope of work and requirements:

1) Design a completely all new, creative, and beautiful menu, including cover page, blue fern oven intro. page, interior pages, and kids menu page.

2) Design a take out edition of the menu. It will be exactly the same as the dine-in menu, but with the addition of a back cover page with info such as contacts, social media, location map, etc…

3) Files are required in Adobe Illustrator format. Layers should be organized, all text should be editable, and all the food pictures easy to change.

4) This is a two language menu, so you are required to make space in the design for a second language. The easiest way to do that is have every item listed in English twice, then I will edit the second text with Illustrator.

5) In your initial design submission, the minimum you are required to submit are these 4 pages:
– Cover page
– Typical interior menu page
– Kids menu page
– Take-out menu back cover page

If your initial design is selected, then you are required to submit all remaining pages to complete the project.

In the link below, you will find:
1) Logo
2) New menu text in Excel
3) Food images (will take some time to upload)
4) The old dine-in and take out menu designs

https://www.filevaultra.com/sh/kq7tmwzabe3pxd/BBBrTnpLk41QaWmZpQ8V2X7Jd?dl=0

Thank you for stopping by and reading this brief. I hope you like this project and enjoy designing our new menu. Please let me know if you have any questions.

Cheers!

Project Deadline Extended
Reason: We have decided to extend the deadline due to the low number of submissions which was much lower than the expected submissions we were give by Brief Harbor.

```html
<!DOCTYPE html>
<html lang="en">
<head>
<meta charset="utf-8">
<title>Menu – Interior Page</title>
<link rel="stylesheet" href="https://fonts.googleapis.com/css2?family=Raleway:wght@300;400&family=Montserrat:wght@700&family=Open+Sans:wght@400&family=Noto+Naskh+Arabic:wght@400;700&display=swap">
<style>
  :root {
    --page-bg: #2a2a2a;
    --page-bg-light: #333333;
    --ink: #ffffff;
    --ink-soft: #9a9a9a;
    --rule: #bdbdbd;
    --sketch: #383838;
    --pizza-main: #b4463f;
    --pizza-crust: #d9a869;
    --juice-main: #f08a1c;
    --juice-light: #fbe3c2;
  }
  html, body {
    margin: 0;
    padding: 0;
    overflow: hidden;
    background: var(--page-bg);
  }
  .menu-page {
    position: relative;
    width: 684px;
    height: 1200px;
    overflow: hidden;
    background: radial-gradient(ellipse at 50% 40%, var(--page-bg-light), var(--page-bg) 75%);
    color: var(--ink);
  }
  .section-heading {
    position: absolute;
    top: 50px;
    margin: 0;
    font: 300 25px/1 "Raleway", sans-serif;
    letter-spacing: 2px;
  }
  .section-heading--beverages { left: 84px; }
  .section-heading--dessert { left: 452px; }
  .rule {
    position: absolute;
    height: 1px;
    background: var(--rule);
  }
  .rule--top { top: 94px; left: 80px; width: 524px; }
  .rule--bottom { top: 1135px; left: 80px; width: 524px; }
  .rule--short { width: 128px; }
  .rule--left { left: 90px; }
  .rule--right { left: 466px; }

  .sketch {
    position: absolute;
    border-radius: 50%;
    background: var(--sketch);
  }

  .dish {
    position: absolute;
    width: 250px;
    text-align: center;
  }
  .dish--left { left: 104px; }
  .dish--right { left: 398px; }
  .dish-name {
    margin: 0;
    font: 700 14px/1.3 "Montserrat", sans-serif;
    letter-spacing: 0.2px;
  }
  .dish-name-ar {
    font-family: "Noto Naskh Arabic", serif;
    font-weight: 700;
  }
  .dish-name-ar--block {
    display: block;
    font-size: 13px;
    line-height: 1.4;
  }
  .dish-desc {
    margin: 14px auto 0;
    width: 170px;
    font: 400 10.5px/1.45 "Open Sans", sans-serif;
    color: var(--ink-soft);
  }
  .dish-desc-ar {
    margin: 12px auto 0;
    width: 180px;
    font: 400 11px/1.6 "Noto Naskh Arabic", serif;
    color: var(--ink-soft);
    direction: rtl;
  }
  .dish--short .dish-desc { margin-top: 10px; }
  .dish--short .dish-desc-ar { margin-top: 8px; }

  .photo {
    position: absolute;
  }
  .photo--pizza {
    left: 390px; top: 158px; width: 182px; height: 98px;
    background: radial-gradient(ellipse at 50% 55%, var(--pizza-main) 0%, #c8684a 45%, var(--pizza-crust) 75%, #efe6dc 100%);
  }
  .photo--juice {
    left: 88px; top: 497px; width: 164px; height: 120px;
    background: linear-gradient(100deg, var(--juice-light) 0%, var(--juice-main) 45%, #f6a23a 75%, var(--juice-light) 100%);
  }
</style>
</head>
<body>
<main class="menu-page">

  <h2 class="section-heading section-heading--beverages">BEVERAGES</h2>
  <h2 class="section-heading section-heading--dessert">DESSERT</h2>
  <div class="rule rule--top"></div>

  <div class="sketch" style="left:318px;top:30px;width:50px;height:56px" role="img" aria-label="Line sketch of a drink glass"></div>
  <div class="sketch" style="left:146px;top:100px;width:22px;height:22px" role="img" aria-label="Small drink sketch"></div>
  <div class="sketch" style="left:174px;top:100px;width:22px;height:22px" role="img" aria-label="Small drink sketch"></div>
  <div class="sketch" style="left:202px;top:100px;width:22px;height:22px" role="img" aria-label="Small drink sketch"></div>
  <div class="sketch" style="left:480px;top:100px;width:22px;height:22px" role="img" aria-label="Small dessert sketch"></div>
  <div class="sketch" style="left:508px;top:100px;width:22px;height:22px" role="img" aria-label="Small dessert sketch"></div>
  <div class="sketch" style="left:536px;top:100px;width:22px;height:22px" role="img" aria-label="Small dessert sketch"></div>
  <div class="sketch" style="left:326px;top:246px;width:30px;height:30px" role="img" aria-label="Sketch of a dessert"></div>
  <div class="sketch" style="left:330px;top:380px;width:28px;height:32px" role="img" aria-label="Sketch of a fruit"></div>
  <div class="sketch" style="left:324px;top:455px;width:26px;height:26px" role="img" aria-label="Sketch of a fruit"></div>
  <div class="sketch" style="left:330px;top:526px;width:24px;height:24px" role="img" aria-label="Sketch of a fruit"></div>
  <div class="sketch" style="left:360px;top:596px;width:40px;height:44px" role="img" aria-label="Sketch of a drink glass"></div>
  <div class="sketch" style="left:318px;top:752px;width:44px;height:44px" role="img" aria-label="Sketch of a cake slice"></div>
  <div class="sketch" style="left:322px;top:850px;width:34px;height:34px" role="img" aria-label="Sketch of a cupcake"></div>
  <div class="sketch" style="left:330px;top:920px;width:30px;height:34px" role="img" aria-label="Sketch of an ice cream cone"></div>
  <div class="sketch" style="left:320px;top:972px;width:36px;height:36px" role="img" aria-label="Sketch of a dessert"></div>
  <div class="sketch" style="left:280px;top:1095px;width:30px;height:44px" role="img" aria-label="Sketch of a glass"></div>
  <div class="sketch" style="left:320px;top:1088px;width:40px;height:52px" role="img" aria-label="Sketch of a milkshake"></div>
  <div class="sketch" style="left:372px;top:1095px;width:30px;height:44px" role="img" aria-label="Sketch of a sundae"></div>

  <article class="dish dish--left" style="top:160px">
    <h3 class="dish-name">CAHSHEW CHICKEN TERIYAKI | <span class="dish-name-ar dish-name-ar--block">دجاج ترياكي بالكاجو</span></h3>
    <p class="dish-desc">Teriyaki chicken, roasted cashews, scallions, sesame, mozzarella cheese. 17</p>
    <p class="dish-desc-ar">دجاج ترياكي، كاجو محمص، بصل أخضر، سمسم، جبن موزاريلا. 17</p>
  </article>

  <div class="photo photo--pizza" role="img" aria-label="Photo of a baked pizza"></div>

  <article class="dish dish--left" style="top:340px">
    <h3 class="dish-name">SPICEY BEEF | <span class="dish-name-ar">لحم حار</span></h3>
    <p class="dish-desc">Spicy ground beef, jalapeños, red onions, bell peppers, cheddar. 17</p>
    <p class="dish-desc-ar">لحم مفروم حار، هالابينو، بصل أحمر، فلفل رومي. 17</p>
  </article>

  <article class="dish dish--right" style="top:340px">
    <h3 class="dish-name">PEPPERONI | <span class="dish-name-ar">بيبروني</span></h3>
    <p class="dish-desc">Pepperoni slices, mozzarella, tomato sauce. 17</p>
    <p class="dish-desc-ar">شرائح بيبروني، موزاريلا، صلصة طماطم. 17</p>
  </article>

  <div class="photo photo--juice" role="img" aria-label="Photo of orange juice in a jug and glass with oranges"></div>

  <article class="dish dish--right" style="top:488px">
    <h3 class="dish-name">GREEK | <span class="dish-name-ar">يوناني</span></h3>
    <p class="dish-desc">Tomatoes, kalamata olives, feta, red onions, green peppers, oregano, mozzarella. 17</p>
    <p class="dish-desc-ar">طماطم، زيتون، جبن فيتا، بصل أحمر، فلفل أخضر، زعتر. 17</p>
  </article>

  <div class="rule rule--short rule--left" style="top:672px"></div>
  <div class="rule rule--short rule--right" style="top:672px"></div>

  <article class="dish dish--left" style="top:690px">
    <h3 class="dish-name">BEEF TERIYAKI PIZZA | <span class="dish-name-ar dish-name-ar--block">بيتزا لحم ترياكي</span></h3>
    <p class="dish-desc">Teriyaki beef, roasted peppers, red onions, mozzarella cheese. 18</p>
    <p class="dish-desc-ar">لحم ترياكي، فلفل مشوي، بصل أحمر، جبن موزاريلا. 18</p>
  </article>

  <article class="dish dish--right" style="top:690px">
    <h3 class="dish-name">BEEF TERIYAKI PIZZA | <span class="dish-name-ar dish-name-ar--block">بيتزا لحم ترياكي</span></h3>
    <p class="dish-desc">Teriyaki beef, roasted peppers, red onions, mozzarella cheese. 18</p>
    <p class="dish-desc-ar">لحم ترياكي، فلفل مشوي، بصل أحمر، جبن موزاريلا. 18</p>
  </article>

  <div class="rule rule--short rule--left" style="top:848px"></div>
  <div class="rule rule--short rule--right" style="top:848px"></div>

  <article class="dish dish--left dish--short" style="top:892px">
    <h3 class="dish-name">VEGGIE | <span class="dish-name-ar">نباتي</span></h3>
    <p class="dish-desc">Mushrooms, green peppers, onions, black olives. 15</p>
    <p class="dish-desc-ar">فطر، فلفل أخضر، بصل، زيتون أسود. 15</p>
  </article>

  <article class="dish dish--right dish--short" style="top:892px">
    <h3 class="dish-name">VEGGIE | <span class="dish-name-ar">نباتي</span></h3>
    <p class="dish-desc">Mushrooms, green peppers, onions, black olives. 15</p>
    <p class="dish-desc-ar">فطر، فلفل أخضر، بصل، زيتون أسود. 15</p>
  </article>

  <div class="rule rule--short rule--left" style="top:1003px"></div>
  <div class="rule rule--short rule--right" style="top:1003px"></div>

  <article class="dish dish--left dish--short" style="top:1022px">
    <h3 class="dish-name">VEGGIE | <span class="dish-name-ar">نباتي</span></h3>
    <p class="dish-desc">Mushrooms, green peppers, onions, black olives. 15</p>
    <p class="dish-desc-ar">فطر، فلفل أخضر، بصل، زيتون أسود. 15</p>
  </article>

  <article class="dish dish--right dish--short" style="top:1022px">
    <h3 class="dish-name">VEGGIE | <span class="dish-name-ar">نباتي</span></h3>
    <p class="dish-desc">Mushrooms, green peppers, onions, black olives. 15</p>
    <p class="dish-desc-ar">فطر، فلفل أخضر، بصل، زيتون أسود. 15</p>
  </article>

  <div class="rule rule--bottom"></div>

</main>
</body>
</html>
```